Fast Growing Personal Injury Law Firm Needs Business Card Design

We need a business card design for a fast growing personal injury law firm in Florida. Our name is Dorian Kalvenfeld, P.A. Our practice is comprised of younger attorneys (in their 30s) that employ more modern techniques/tools than our older competition. We would prefer a look that is a modern play on a classic look. Also, we would like to continue using a color scheme that employs navy blue and kelly green (other shades of green could be fine too) as well as our "E" logo.

Industry/Entity Type

Law Firm

```html
<!DOCTYPE html>
<html lang="en">
<head>
<meta charset="utf-8">
<title>Dorian Kalvenfeld, P.A. — Business Card</title>
<link rel="stylesheet" href="https://fonts.googleapis.com/css2?family=Cinzel:wght@500;600&family=Lato:wght@400&display=swap">
<style>
  :root {
    --navy: #0d2a5c;
    --green: #16803e;
    --ink: #2f2f2f;
    --rule: #6b6b6b;
    --divider: #c9c9c9;
    --paper: #ffffff;
    --stage: #4a4a4a;
  }
  * { margin: 0; padding: 0; box-sizing: border-box; }
  html, body { width: 1200px; height: 820px; overflow: hidden; }
  body { background: var(--stage); position: relative; font-family: "Lato", Arial, sans-serif; }

  .card { position: absolute; top: 258px; width: 477px; height: 273px; overflow: hidden; }
  .card--front { left: 115px; background: var(--paper); }
  .card--back { left: 621px; background: var(--navy); }

  /* Front: brand lockup */
  .brand-square { position: absolute; left: 52px; top: 42px; width: 71px; height: 62px; background: var(--green); }
  .brand-name {
    position: absolute; left: 136px; top: 46px;
    font-family: "Cinzel", "Times New Roman", serif; font-weight: 600;
    font-size: 23px; color: var(--navy); letter-spacing: 0.3px; white-space: nowrap;
  }
  .brand-rule { position: absolute; left: 136px; top: 75px; width: 262px; height: 1px; background: var(--navy); }
  .brand-tagline {
    position: absolute; left: 136px; top: 78px;
    font-family: "Cinzel", "Times New Roman", serif; font-weight: 500;
    font-size: 15.5px; color: var(--green); letter-spacing: 1.6px; white-space: nowrap;
  }

  /* Front: person */
  .person { position: absolute; left: 50px; top: 146px; width: 184px; }
  .person__name { font-size: 16.5px; color: var(--navy); line-height: 20px; }
  .person__title { font-size: 12.5px; color: var(--ink); line-height: 18px; margin-top: 2px; padding-bottom: 3px; border-bottom: 1px solid var(--rule); }
  .person__address { font-size: 12.5px; color: var(--ink); line-height: 16px; margin-top: 6px; white-space: nowrap; }

  .divider { position: absolute; left: 254px; top: 148px; width: 1px; height: 76px; background: var(--divider); }

  /* Front: contact list */
  .contacts { position: absolute; left: 281px; top: 146px; list-style: none; }
  .contacts li { display: flex; align-items: center; height: 20px; font-size: 12.5px; color: var(--ink); }
  .contacts svg { width: 11px; height: 11px; margin-right: 4px; flex: none; }

  .card-band { position: absolute; left: 0; bottom: 0; width: 477px; height: 17px; }

  /* Back */
  .back-lockup { position: absolute; left: 0; top: 113px; width: 100%; text-align: center; color: var(--paper); }
  .back-lockup__name { font-family: "Cinzel", "Times New Roman", serif; font-weight: 600; font-size: 21px; letter-spacing: 0.4px; line-height: 26px; }
  .back-lockup__tagline { font-family: "Cinzel", "Times New Roman", serif; font-weight: 500; font-size: 14.5px; letter-spacing: 1.7px; line-height: 20px; }
  .back-lockup__rule { width: 256px; height: 2px; background: var(--green); margin: 2px auto 3px; }
  .back-lockup__web { font-family: "Cinzel", "Times New Roman", serif; font-weight: 500; font-size: 12px; letter-spacing: 3.6px; line-height: 16px; }
</style>
</head>
<body>

<section class="card card--front" aria-label="Business card front">
  <div class="brand-square"></div>
  <div class="brand-name">Dorian Kalvenfeld, P.A.</div>
  <div class="brand-rule"></div>
  <div class="brand-tagline">Personal Injury Attorneys</div>

  <div class="person">
    <p class="person__name">Dorian Kalvenfeld</p>
    <p class="person__title">Attorney at Law</p>
    <p class="person__address">2215 Harbor Point Drive Suite 410<br>Palm Haven, Florida 34290</p>
  </div>

  <div class="divider"></div>

  <ul class="contacts">
    <li>
      <svg viewBox="0 0 12 12"><circle cx="6" cy="6" r="6" fill="#0d2a5c"/><path d="M3.6 3.2l1.2-.4.8 1.6-.7.6c.4.8 1 1.4 1.8 1.8l.6-.7 1.6.8-.4 1.2c-2.6-.2-4.7-2.3-4.9-4.9z" fill="#fff"/></svg>
      941.555.0148
    </li>
    <li>
      <svg viewBox="0 0 12 12"><circle cx="6" cy="6" r="6" fill="#0d2a5c"/><rect x="3.5" y="3" width="5" height="6" rx="0.6" fill="#fff"/><rect x="4.4" y="4" width="3.2" height="1.4" fill="#0d2a5c"/></svg>
      941.555.0172
    </li>
    <li>
      <svg viewBox="0 0 12 12"><circle cx="6" cy="6" r="6" fill="#0d2a5c"/><rect x="3" y="4" width="6" height="4.2" fill="#fff"/><path d="M3 4l3 2.3L9 4" fill="none" stroke="#0d2a5c" stroke-width="0.7"/></svg>
      dorian@kalvenfeldlaw.com
    </li>
    <li>
      <svg viewBox="0 0 12 12"><circle cx="6" cy="6" r="6" fill="#0d2a5c"/><circle cx="6" cy="6" r="3.2" fill="none" stroke="#fff" stroke-width="0.8"/><path d="M2.8 6h6.4M6 2.8c-1.4 1.8-1.4 4.6 0 6.4M6 2.8c1.4 1.8 1.4 4.6 0 6.4" fill="none" stroke="#fff" stroke-width="0.6"/></svg>
      www.kalvenfeldlaw.com
    </li>
  </ul>

  <svg class="card-band" viewBox="0 0 477 17" preserveAspectRatio="none" aria-hidden="true">
    <polygon points="0,0 253,0 246,11 0,11" fill="#16803e"/>
    <polygon points="259,0 477,0 477,17 0,17 0,13 250,13" fill="#0d2a5c"/>
  </svg>
</section>

<section class="card card--back" aria-label="Business card back">
  <div class="back-lockup">
    <p class="back-lockup__name">Dorian Kalvenfeld, P.A.</p>
    <p class="back-lockup__tagline">Personal Injury Attorneys</p>
    <div class="back-lockup__rule"></div>
    <p class="back-lockup__web">WWW.KALVENFELDLAW.COM</p>
  </div>
</section>

</body>
</html>
```